WordPress Design for both website and landing page for an expert

I need a clean and stylish design for my new website. I work as an expert (see attached file WHY HOW WHAT), my product is expert opinion (reports) for company evaluations You can use all of the attached pictures colored or black / white. The person is me, you can add other pictures, if you want. The design should be clean and stylish, so you could use white, black, gray, silver and / or one additional color. I have added an idea about my website, see attached file CONCEPT WEBSITE If you have any more information, please do not hesitate to contact us 'Hesitate to ask me ...

```html
<!DOCTYPE html>
<html lang="en">
<head>
<meta charset="utf-8">
<title>Milan Hartwig – Why / How I do</title>
<link href="https://fonts.googleapis.com/css2?family=Montserrat:wght@400;500;600&family=Noto+Serif:wght@400&display=swap" rel="stylesheet">
<style>
  :root {
    --ink: #24262b;
    --muted: #80858d;
    --nav-active: #9a9ea5;
    --band: #eff2f5;
    --footer: #3a3d45;
    --footer-text: #b4b8bf;
    --icon-bg: #eef1f4;
    --icon-line: #5b606a;
    --hero-a: #c9d4df;
    --hero-b: #7f93a8;
    --hero-c: #3c4654;
    --white: #ffffff;
  }
  * { margin: 0; padding: 0; box-sizing: border-box; }
  html, body { width: 893px; height: 1200px; overflow: hidden; background: var(--white); }
  body { position: relative; font-family: "Montserrat", sans-serif; color: var(--ink); }

  .brand { position: absolute; left: 50px; top: 36px; display: flex; align-items: center; gap: 10px; }
  .brand-dot { width: 14px; height: 14px; background: var(--ink); }
  .brand-name { font-size: 15px; font-weight: 500; letter-spacing: 2.6px; text-transform: uppercase; color: var(--ink); }

  .main-nav { position: absolute; top: 44px; right: 51px; display: flex; gap: 26px; }
  .main-nav a { font-size: 9.5px; font-weight: 600; letter-spacing: 1.6px; text-transform: uppercase; color: var(--ink); text-decoration: none; }
  .main-nav a.is-active { color: var(--nav-active); }

  .hero { position: absolute; left: 102px; top: 146px; width: 688px; height: 280px;
    background: linear-gradient(125deg, var(--hero-c) 0%, var(--hero-b) 30%, var(--hero-a) 60%, #e6ecf2 80%, var(--hero-b) 100%);
    display: flex; align-items: center; justify-content: center; }
  .hero-title { font-size: 31px; font-weight: 500; letter-spacing: 3px; line-height: 38px; text-align: center; color: var(--white); text-transform: uppercase; margin-top: -40px; }

  .serif { font-family: "Noto Serif", serif; font-size: 11.3px; line-height: 19px; color: var(--muted); }
  .intro { position: absolute; left: 210px; top: 474px; width: 476px; }
  .how-title { position: absolute; left: 210px; top: 571px; font-size: 20px; font-weight: 500; color: var(--ink); }
  .how-text { position: absolute; left: 210px; top: 605px; width: 350px; }

  .step { position: absolute; top: 690px; width: 220px; }
  .step-icon { width: 94px; height: 94px; border-radius: 50%; background: var(--icon-bg); display: flex; align-items: center; justify-content: center; }
  .step-text { margin-top: 14px; }
  .step--process { left: 210px; }
  .step--valuation { left: 472px; width: 200px; }

  .cta-band { position: absolute; left: 0; top: 941px; width: 893px; height: 206px; background: var(--band); text-align: center; }
  .cta-title { margin-top: 45px; font-size: 20px; font-weight: 500; line-height: 29px; color: var(--ink); }
  .cta-button { display: inline-block; margin-top: 25px; width: 159px; height: 29px; line-height: 27px; border: 1px solid #8d9199; border-radius: 15px; font-size: 9px; font-weight: 600; letter-spacing: 1.2px; color: var(--ink); text-decoration: none; text-transform: uppercase; }

  .site-footer { position: absolute; left: 0; top: 1147px; width: 893px; height: 53px; background: var(--footer); }
  .copyright { position: absolute; left: 102px; top: 22px; font-size: 8.5px; color: var(--footer-text); }
  .legal-links { position: absolute; right: 102px; top: 22px; font-size: 8.5px; color: var(--footer-text); display: flex; gap: 10px; }
  .legal-links a { color: var(--footer-text); text-decoration: none; }
  .to-top { position: absolute; left: 826px; top: 11px; width: 32px; height: 32px; border-radius: 50%; background: #8d9199; display: flex; align-items: center; justify-content: center; }
</style>
</head>
<body>
  <header class="site-header">
    <div class="brand"><span class="brand-dot"></span><span class="brand-name">Milan Hartwig</span></div>
    <nav class="main-nav">
      <a href="#">Home</a>
      <a href="#">About</a>
      <a href="#">What I do</a>
      <a href="#" class="is-active">Why / How I do</a>
      <a href="#">Contact</a>
    </nav>
  </header>

  <section class="hero" role="img" aria-label="Photo of hands pointing a pen at printed financial bar charts on a desk">
    <h1 class="hero-title">Economy is my<br>passion</h1>
  </section>

  <p class="intro serif">Economy is made in numbers. Sometimes it is difficult to find the right numbers. I am always interested in finding out, how economy works and which numbers will tell the really true story. I want to know it ...</p>

  <h2 class="how-title">How I do?</h2>
  <p class="how-text serif">Each report begins with understanding. So I ask you questions and listen very carefully.</p>

  <div class="step step--process">
    <div class="step-icon">
      <svg width="46" height="46" viewBox="0 0 46 46" fill="none" stroke="var(--icon-line)" stroke-width="1.4">
        <path d="M4 40h38"/>
        <rect x="7" y="26" width="5" height="14"/>
        <rect x="14" y="20" width="5" height="20"/>
        <path d="M22 6h18v22"/>
        <circle cx="28" cy="26" r="7"/>
        <path d="M33 31l7 7"/>
        <path d="M25 26l2 2 4-4"/>
      </svg>
    </div>
    <p class="step-text serif">In the preparation of each report I follow one defined process, but which is tailored to the particular each company is customized.</p>
  </div>

  <div class="step step--valuation">
    <div class="step-icon">
      <svg width="46" height="46" viewBox="0 0 46 46" fill="none" stroke="var(--icon-line)" stroke-width="1.4">
        <rect x="5" y="5" width="18" height="24" rx="1"/>
        <rect x="8" y="8" width="12" height="5"/>
        <path d="M9 17h2M14 17h2M19 17h1M9 21h2M14 21h2M19 21h1M9 25h2M14 25h2"/>
        <path d="M16 14h22l3 4v23H16z"/>
        <circle cx="31" cy="30" r="7"/>
        <path d="M33 27h-3a1.5 1.5 0 0 0 0 3h2a1.5 1.5 0 0 1 0 3h-3M31 25v2M31 33v2"/>
        <path d="M19 36h6"/>
      </svg>
    </div>
    <p class="step-text serif">This approach, coupled with specialization in the area business valuation, allows orders very fast &amp; at the same time correct and impeccable handle</p>
  </div>

  <section class="cta-band">
    <h2 class="cta-title">You need an opinion to determine<br>the value of your company</h2>
    <a href="#" class="cta-button">Contact now!</a>
  </section>

  <footer class="site-footer">
    <p class="copyright">© 2018 Milan R. Hartwig. All Rights Reserved</p>
    <nav class="legal-links">
      <a href="#">Data protection</a><span>I</span>
      <a href="#">Cookies</a><span>I</span>
      <a href="#">imprint</a>
    </nav>
    <a href="#" class="to-top" aria-label="Back to top">
      <svg width="10" height="10" viewBox="0 0 10 10" fill="none" stroke="#ffffff" stroke-width="1"><path d="M5 9V1M2 4l3-3 3 3"/></svg>
    </a>
  </footer>
</body>
</html>
```